Mobile Friendly Lead Generation Landing Page

We are a web marketing company that specialized in web lead generation. Recently we have started buying media from mobile devices and we need a mobile interface(landing page) where we can collect user data in an effective manner.

Our current mobile landing page is:
http://www.tutorpath.example.com/lp13d/index.aspx?a=true&source=841356
Through this you can see what the steps/questions users need to answer to get matched to a school. We need the design for the whole process.

We are pretty open for design ideas and our goal is to make this mobile optimized landing page have the look and feel of an app...but not an app.
There are several questions in the process but we are open to changing the way they are presented. As in, you can have one question at a time or a few.
The goal is to make this EXTREMELY EASY for users to interact with.

One example that we have liked is:
http://learnvane.example/schools/57214-page1.lvne (please note that this opens only on mobile devices)

Some of these screenshots are attached.

Our web form looks like this:
http://www.tutorpath.example.com/lp88/index.aspx?a=true

```html
<!DOCTYPE html>
<html lang="en">
<head>
<meta charset="utf-8">
<title>Field of Interest – Step Form</title>
<link rel="stylesheet" href="https://fonts.googleapis.com/css2?family=Open+Sans:wght@300;400;600;700&display=swap">
<style>
  :root {
    --header-bg: #3d5068;
    --progress-bg: #243246;
    --track: #3a4c63;
    --track-edge: #2f3f54;
    --green-dark: #2f9a1c;
    --green-light: #7dc54c;
    --progress-text: #6f7d8e;
    --page-bg: #e8e8e8;
    --card-bg: #ffffff;
    --card-edge: #d9d9d9;
    --title: #8a8a8a;
    --btn-bg: #ececec;
    --btn-edge: #c9c9c9;
    --btn-text: #a3a3a3;
    --btn-active: #7dc54c;
    --btn-active-edge: #5fa033;
    --white: #ffffff;
  }
  * { box-sizing: border-box; margin: 0; padding: 0; }
  html, body {
    width: 725px; height: 1200px; overflow: hidden;
    font-family: "Open Sans", sans-serif;
    background: var(--page-bg);
  }
  .screen { width: 725px; height: 1200px; display: flex; flex-direction: column; }

  .top-bar {
    height: 100px; background: var(--header-bg);
    display: flex; align-items: center; justify-content: space-between;
    padding: 0 48px 0 48px;
  }
  .top-bar svg { width: 40px; height: 40px; display: block; }
  .top-bar__title { color: var(--white); font-size: 26px; font-weight: 400; }
  .top-bar__title strong { font-weight: 700; }

  .progress {
    height: 190px; background: var(--progress-bg);
    padding-top: 62px;
  }
  .progress__track {
    display: flex; gap: 9px; margin-left: 88px; width: 560px; height: 38px;
  }
  .progress__step {
    background: var(--track); border: 1px solid var(--track-edge); border-radius: 3px;
    position: relative; overflow: hidden;
  }
  .progress__step--done { width: 122px; background: var(--green-dark); }
  .progress__step--current { width: 264px; }
  .progress__step--current .progress__fill {
    position: absolute; left: 0; top: 0; bottom: 0; width: 97px; background: var(--green-light);
  }
  .progress__step--next { width: 147px; background: #44566e; }
  .progress__label {
    text-align: center; color: var(--progress-text); font-size: 15px; margin-top: 20px; font-weight: 300;
  }

  .form-area { flex: 1; padding: 34px 28px 0; }
  .form-card {
    width: 669px; height: 836px; background: var(--card-bg);
    border: 1px solid var(--card-edge); border-radius: 4px;
    padding: 0 35px;
  }
  .form-card__title {
    text-align: center; color: var(--title); font-weight: 300; font-size: 34px;
    margin-top: 42px; height: 80px;
  }
  .field-grid {
    display: grid; grid-template-columns: 280px 280px; column-gap: 39px; row-gap: 23px;
    list-style: none; margin-top: 35px;
  }
  .field-option {
    height: 59px; background: var(--btn-bg); border-radius: 3px;
    box-shadow: 0 2px 0 var(--btn-edge);
    display: flex; align-items: center; justify-content: center;
    color: var(--btn-text); font-weight: 700; font-size: 17px; text-transform: uppercase;
  }
  .field-option--selected {
    background: var(--btn-active); color: var(--white); box-shadow: 0 2px 0 var(--btn-active-edge);
  }
</style>
</head>
<body>
<main class="screen">
  <header class="top-bar">
    <svg viewBox="0 0 40 40" aria-label="Back">
      <circle cx="20" cy="20" r="17" fill="none" stroke="#8796a8" stroke-width="2"/>
      <path d="M28 20H13M19 13l-7 7 7 7" fill="none" stroke="#8796a8" stroke-width="2.4" stroke-linecap="round" stroke-linejoin="round"/>
    </svg>
    <h1 class="top-bar__title">Fill out our <strong>2 MINUTE</strong> form!</h1>
    <svg viewBox="0 0 40 40" aria-label="Next">
      <circle cx="20" cy="20" r="17" fill="none" stroke="#8796a8" stroke-width="2"/>
      <path d="M12 20h15M21 13l7 7-7 7" fill="none" stroke="#8796a8" stroke-width="2.4" stroke-linecap="round" stroke-linejoin="round"/>
    </svg>
  </header>

  <section class="progress">
    <div class="progress__track">
      <div class="progress__step progress__step--done"></div>
      <div class="progress__step progress__step--current"><div class="progress__fill"></div></div>
      <div class="progress__step progress__step--next"></div>
    </div>
    <p class="progress__label">progress : 76% completed</p>
  </section>

  <section class="form-area">
    <div class="form-card">
      <h2 class="form-card__title">Please select your field of interest :</h2>
      <ul class="field-grid">
        <li class="field-option">Art &amp; Design</li>
        <li class="field-option">Liberal Arts</li>
        <li class="field-option field-option--selected">Business</li>
        <li class="field-option">Nursing</li>
        <li class="field-option">Criminal Justice</li>
        <li class="field-option">Political Science</li>
        <li class="field-option">Education &amp; Teaching</li>
        <li class="field-option">Psychology</li>
        <li class="field-option">Engineering</li>
        <li class="field-option">Religious Studies</li>
        <li class="field-option">Health Care</li>
        <li class="field-option">Science &amp; Math</li>
        <li class="field-option">Human Services</li>
        <li class="field-option">Social Services</li>
        <li class="field-option">Legal &amp; Paralegal</li>
        <li class="field-option">Technology</li>
      </ul>
    </div>
  </section>
</main>
</body>
</html>
```